Private Dining Restaurant Menu Design

Looking for help in designing a private dining room menu brochure - probably would need 4 panel layout to make all of the content fit, or a 5.5x8" booklet. Open to your ideas on layout/vessel - would want to post on website and be able to print to hand out to guests interested in booking our private dining room.

All content is in the attached "Private Dining Menu".

Would like to match existing dinner menu design - also attached.

Website is www.copperkettlebistro.com

Requirements
Must have
• Easy to read format of a brochure of the private dining menu content - want to be able to hand out to interested guests and have it simple and easy to read/flip through.

```html
<!DOCTYPE html>
<html lang="en">
<head>
<meta charset="utf-8">
<title>Private Dining Menu</title>
<link href="https://fonts.googleapis.com/css2?family=Josefin+Sans:wght@600;700&family=Oswald:wght@400;500&family=Jost:ital,wght@0,400;0,500;1,500;1,600&display=swap" rel="stylesheet">
<style>
:root{
  --backdrop:#f2f2f2;
  --paper:#ffffff;
  --linen:#e8e4d6;
  --linen-soft:#efece2;
  --rust:#8e2b2a;
  --rust-soft:#b9726f;
  --navy:#1f2b5c;
  --navy-soft:#6f779a;
  --ink:#1b1b1b;
  --grain:#e4e0d2;
}
*{margin:0;padding:0;box-sizing:border-box}
html,body{width:1200px;height:900px;overflow:hidden;background:var(--backdrop)}
body{position:relative;font-family:"Oswald",sans-serif;color:var(--ink)}
.spread{position:absolute;left:52px;top:50px;width:1098px;height:800px;background:var(--paper);box-shadow:0 2px 6px rgba(0,0,0,.18)}
.page-left{position:absolute;left:0;top:0;width:548px;height:800px;background:var(--paper);overflow:hidden}
.grain-decor{position:absolute;background:radial-gradient(ellipse at center,var(--grain) 0%,rgba(228,224,210,.4) 55%,rgba(255,255,255,0) 75%)}
.grain-top{left:-60px;top:-60px;width:300px;height:220px}
.grain-bottom{left:-80px;top:520px;width:640px;height:340px}
.page-right{position:absolute;left:548px;top:0;width:550px;height:800px;background:var(--linen)}
.title-row{position:absolute;left:0;top:14px;width:548px;height:80px}
.art-panel{position:absolute;border-radius:4px}
.art-navy{top:4px;width:94px;height:68px;background:linear-gradient(180deg,var(--navy-soft) 0%,var(--navy) 100%)}
.art-left{left:96px}
.art-right{left:358px}
.menu-title{position:absolute;left:198px;top:28px;width:150px;text-align:center;font-family:"Josefin Sans",sans-serif;font-weight:700;font-size:44px;color:var(--rust);letter-spacing:1px}
.box{position:absolute;left:50px;width:449px}
.box-appetizers{top:113px;height:318px;background:var(--linen-soft);border:1px solid var(--rust)}
.box-platters{top:457px;height:291px;border:1px solid var(--navy);background:var(--paper)}
.rule-heading{position:absolute;left:0;width:100%;display:flex;align-items:center;justify-content:center;gap:12px;font-family:"Josefin Sans",sans-serif;font-weight:700;letter-spacing:1px}
.rule-heading::before,.rule-heading::after{content:"";display:block;height:1.5px;background:currentColor}
.box .rule-heading::before,.box .rule-heading::after{width:86px}
.box-appetizers .rule-heading{top:32px;font-size:25px;color:var(--rust)}
.box-platters .rule-heading{top:26px;font-size:25px;color:var(--navy)}
.note{position:absolute;left:0;width:100%;text-align:center;font-family:"Jost",sans-serif;font-style:italic;font-weight:600;font-size:13.5px;line-height:1.35}
.box-appetizers .note{top:66px}
.box-platters .note{top:63px}
.app-list{position:absolute;left:35px;top:94px;list-style:none}
.app-list li{font-size:17px;font-weight:500;line-height:1.2;margin-bottom:7px;letter-spacing:.2px}
.price{font-family:"Jost",sans-serif;font-style:italic;font-weight:600;font-size:15px}
.sub{display:block;font-size:10.5px;font-weight:400;letter-spacing:.3px;line-height:1.2}
.art-rust{left:334px;top:116px;width:82px;height:146px;background:linear-gradient(180deg,var(--rust-soft) 0%,var(--rust) 100%)}
.platter-list{position:absolute;left:0;top:115px;width:100%;list-style:none;text-align:center}
.platter-list li{font-size:17px;font-weight:500;line-height:1.2;margin-bottom:8px}
.platter-list .price{font-size:14px}
.lunch-heading{top:51px;font-size:26px;color:var(--navy);gap:10px}
.lunch-heading::before,.lunch-heading::after{width:100px}
.page-right .note{top:95px;font-size:13.5px}
.option{position:absolute;left:0;width:100%;text-align:center}
.option-a{top:160px}
.option-b{top:400px}
.option-c{top:596px}
.option-name{font-size:20px;font-weight:500;letter-spacing:.3px}
.option-name .price{font-size:15px}
.detail{font-family:"Jost",sans-serif;font-size:11.5px;line-height:1.35;margin-top:1px}
.group{font-size:16px;font-weight:500;margin-top:4px;line-height:1.2}
.group-items{font-size:11px;letter-spacing:.3px;line-height:1.45}
.dish{font-size:17px;font-weight:500;line-height:1.4;letter-spacing:.2px}
.option-b .dish:first-of-type,.option-c .dish:first-of-type{margin-top:5px}
</style>
</head>
<body>
<main class="spread">
  <section class="page-left">
    <div class="grain-decor grain-top" role="img" aria-label="Faint wood grain texture"></div>
    <div class="grain-decor grain-bottom" role="img" aria-label="Faint wood grain texture"></div>
    <header class="title-row">
      <div class="art-panel art-navy art-left" role="img" aria-label="Navy pine tree illustration"></div>
      <h1 class="menu-title">MENU</h1>
      <div class="art-panel art-navy art-right" role="img" aria-label="Navy pine tree illustration"></div>
    </header>

    <section class="box box-appetizers">
      <h2 class="rule-heading">APPETIZERS</h2>
      <p class="note">Prices are by the dozen</p>
      <ul class="app-list">
        <li>TEXAS EGG ROLLS <span class="price">- $25</span></li>
        <li>CHICKEN WINGS <span class="price">- $12</span><span class="sub">BUFFALO, BBQ, OR BLACKENED</span></li>
        <li>BABY BACK RIBS <span class="price">- $30</span></li>
        <li>SLIDERS <span class="price">- $35</span><span class="sub">PULLED PORK OR ROTISSERIE CHICKEN</span></li>
        <li>WOOD-ROASTED QUESADILLAS <span class="price">- $30</span></li>
        <li>KETTLE SKINS <span class="price">- $25</span></li>
      </ul>
      <div class="art-panel art-rust" role="img" aria-label="Red pine tree illustration"></div>
    </section>

    <section class="box box-platters">
      <h2 class="rule-heading">PLATTERS</h2>
      <p class="note">Small platters serve approximately 10-15 people,<br>large platters serve approximately 25-30.</p>
      <ul class="platter-list">
        <li>CHIPS, SALSA, AND GUACAMOLE <span class="price">- sm$25/lg$45</span></li>
        <li>FRESH FRUIT PLATTER <span class="price">- sm$50/lg$75</span></li>
        <li>HOT ARTICHOKE DIP <span class="price">- sm$30/lg$60</span><span class="sub">SERVED WITH BREAD &amp; TORTILLA CHIPS</span></li>
        <li>DOMESTIC CHEESE AND CRACKERS <span class="price">- sm$45/lg$65</span></li>
        <li>FRESH VEGGIE PLATTER <span class="price">- sm$40/lg$65</span></li>
      </ul>
    </section>
  </section>

  <section class="page-right">
    <h2 class="rule-heading lunch-heading">LUNCH OPTIONS</h2>
    <p class="note">An option must be chosen for groups of 15 or more,<br>served before 3pm</p>

    <article class="option option-a">
      <h3 class="option-name">OPTION A <span class="price">- $10-$12/Person</span></h3>
      <p class="detail">Pick Two Lunch Menu – Soup &amp; Salad ($10), Soup &amp; Sandwich ($11),<br>or Salad &amp; Sandwich ($12)</p>
      <h4 class="group">SANDWICHES</h4>
      <p class="group-items">½ TURKEY CLUB, ½ BLTA, BBQ PORK SLIDERS (2), WOOD-ROASTED ROTISSERIE<br>CHICKEN SLIDERS (2), WALLEYE TACOS (2), OR CHICKEN TACOS (2)</p>
      <h4 class="group">SOUPS</h4>
      <p class="group-items">CHICKEN WILD RICE, WHITE CHICKEN CHILI, OR SOUP OF THE DAY</p>
      <h4 class="group">SALADS</h4>
      <p class="group-items">WEDGE, HOUSE, OR CAESAR SALAD</p>
    </article>

    <article class="option option-b">
      <h3 class="option-name">OPTION B <span class="price">- $13/Person</span></h3>
      <p class="detail">Served with your choice of fries, cheesy hashbrowns, soup, or apple cabbage slaw</p>
      <p class="dish">APPLEWOOD BACON &amp; FAJITA CHICKEN SALAD</p>
      <p class="dish">ROTISSERIE CHICKEN SALAD</p>
      <p class="dish">BROWN SUGAR BACON &amp; SMOKED CHEDDAR BURGER</p>
      <p class="dish">PEPPERJACK TURKEY MELT</p>
      <p class="dish">WALLEYE FISH TACOS</p>
    </article>

    <article class="option option-c">
      <h3 class="option-name">OPTION C <span class="price">- $13/Person Buffet Option</span></h3>
      <p class="detail">Food ready upon arrival, or at a set time of your choice</p>
      <p class="dish">SANDWICH PLATTER</p>
      <p class="group-items">ASSORTED ROTISSERIE TURKEY CLUB, HAM AND CHEESE, AND VEGGIE WRAP</p>
      <p class="dish">ROTISSERIE CHICKEN SALAD BAR</p>
      <p class="dish">FRESH FRUIT PLATTER</p>
      <p class="dish">HOUSE-MADE POTATO CHIPS</p>
    </article>
  </section>
</main>
</body>
</html>
```